Social media app sign-up flow that asks users to give personal info and connect with other apps

Design an interactive, fun, and playful sign-up flow in which you are providing information about you, your interests, and connecting with different API plug-ins such as Chatterloop, Workvine, Tunevale, etc. (using the brand palette attached).

Basic wireframe, and business requirements are also attached.

Target Market(s)

Gen Z + Millennials (ages 22-40)

Font styles to use
Sans Serif

Colors
fbed22
fbee3d
fbf289

Requirements
Must have
• Forms for users to submit their info. Follow the color palette attached.

Connect with Chatterloop, Connect with Workvine, Connect with Tunevale, Connect with Gatherpost buttons
Nice to have
• I like the way you can use cards to submit your information for each category. Interactive card design for providing your info
Should not have
• Basic outdated designs, long forms

```html
<!DOCTYPE html>
<html lang="en">
<head>
<meta charset="utf-8">
<title>Tell me about you – sign-up flow</title>
<link rel="stylesheet" href="https://fonts.googleapis.com/css2?family=Rubik:wght@400;500&display=swap">
<style>
  :root{
    --yellow:#fbed22;
    --yellow-soft:#fbee3d;
    --yellow-pale:#fbf289;
    --ink:#1b1b1b;
    --night-top:#1e0b38;
    --night-bottom:#6a2396;
    --dusk:#8b8fd2;
    --chatterloop:#4a5fa0;
    --workvine:#0e76b8;
    --tunevale:#17c120;
    --white:#ffffff;
    --muted:#8d8d8d;
  }
  *{box-sizing:border-box;margin:0;padding:0}
  html,body{width:1021px;height:1200px;overflow:hidden;background:var(--white)}
  body{position:relative;font-family:"Rubik",sans-serif;color:var(--ink)}

  .brand-band{position:absolute;left:0;top:560px;width:1021px;height:290px;background:var(--yellow);
    clip-path:polygon(0 11px,100% 5px,100% 278px,0 284px)}

  .screen{position:absolute;width:177px;height:383px;overflow:hidden;background:var(--night-top);
    box-shadow:0 4px 22px rgba(0,0,0,.18)}
  .screen--night{background:radial-gradient(circle at 85% 12%,rgba(160,60,200,.45),transparent 35%),
    radial-gradient(circle at 90% 95%,rgba(220,90,220,.6),transparent 30%),
    linear-gradient(180deg,var(--night-top),var(--night-bottom))}
  .screen--deep{background:radial-gradient(circle at 80% 15%,rgba(130,50,170,.4),transparent 35%),
    linear-gradient(180deg,#1c0a2e,#2b0f44)}
  .screen--dusk{background:var(--dusk)}
  .screen--hero{border-radius:20px;width:174px;height:382px}

  .status{position:absolute;top:0;left:0;right:0;height:10px;background:var(--white);
    font-size:5px;font-weight:500;display:flex;align-items:center;padding:0 6px;gap:4px}
  .status .dots{letter-spacing:.5px}
  .status .time{margin-left:22px;font-weight:400}
  .status .icons{margin-left:auto;display:flex;gap:6px;align-items:center}
  .status .wifi{width:6px;height:4px;border:1px solid var(--ink);border-bottom:none;border-radius:6px 6px 0 0}
  .status .battery{width:10px;height:5px;border:1px solid var(--ink);border-radius:1px;
    background:linear-gradient(90deg,var(--ink) 40%,transparent 40%)}

  .screen-title{position:absolute;top:34px;left:0;right:0;text-align:center;color:var(--yellow);
    font-size:12px;font-weight:500}

  .card-grid{position:absolute;top:64px;left:10px;display:grid;grid-template-columns:76px 76px;
    grid-auto-rows:69px;gap:6px}
  .info-card{background:var(--yellow);display:flex;flex-direction:column;align-items:center;
    justify-content:center;gap:4px;text-align:center;font-size:8.4px;font-weight:500;line-height:1.2}
  .info-card svg{width:26px;height:26px;fill:none;stroke:var(--ink);stroke-width:1.5;
    stroke-linecap:round;stroke-linejoin:round}

  .back-arrow{position:absolute;top:17px;left:9px;width:18px;height:8px}
  .signup-title{position:absolute;top:45px;left:9px;color:var(--yellow);font-size:14px;font-weight:500}
  .field{position:absolute;left:7px;width:164px;height:23px;background:var(--white);font-size:7.6px;
    color:#555;display:flex;align-items:center;padding:0 8px;justify-content:space-between}
  .field i{width:5px;height:5px;background:#999;border-radius:1px}
  .primary-btn{position:absolute;left:7px;width:164px;height:23px;background:var(--yellow);
    font-size:8.2px;font-weight:500;display:flex;align-items:center;justify-content:center}
  .remember{position:absolute;left:7px;right:6px;top:159px;display:flex;align-items:center;
    font-size:7.2px;color:var(--white);gap:4px}
  .remember .box{width:10px;height:10px;background:var(--white);border-radius:2px}
  .remember a{margin-left:auto;color:var(--white);text-decoration:underline}
  .divider-or{position:absolute;top:187px;left:0;right:0;text-align:center;color:var(--white);font-size:7.4px}

  .connect-btn{position:absolute;height:22px;display:flex;align-items:center;color:var(--white);
    font-size:7.8px;border-radius:2px}
  .connect-btn .mark{width:25px;height:100%;display:flex;align-items:center;justify-content:center;
    border-right:1px solid rgba(255,255,255,.25)}
  .connect-btn .mark span{width:6px;height:6px;border:1px solid var(--white)}
  .connect-btn .label{flex:1;text-align:center}
  .connect-btn--chatterloop{background:var(--chatterloop)}
  .connect-btn--workvine{background:var(--workvine)}
  .connect-btn--tunevale{background:var(--tunevale);justify-content:center;letter-spacing:.3px}

  .chips{position:absolute;left:9px;display:grid;grid-template-columns:77px 77px;gap:5px 5px}
  .chip{position:relative;height:21px;background:var(--yellow);font-size:8px;display:flex;
    align-items:center;justify-content:center;white-space:nowrap}
  .chip::after{content:"x";position:absolute;top:-3px;right:1px;font-size:6px}
  .search{position:absolute;left:9px;width:159px;background:var(--white)}
  .search .query{height:22px;font-size:8.4px;display:flex;align-items:center;padding-left:8px;
    border-bottom:1px solid #ddd}
  .search .query::after{content:"";width:.6px;height:9px;background:var(--ink);margin-left:1px}
  .search .suggestion{height:22px;font-size:7px;color:var(--muted);display:flex;align-items:center;padding-left:7px}

  .city-photo{position:absolute;left:0;right:0;bottom:0;top:212px;
    background:linear-gradient(180deg,#7f8ab8 0%,#a9a3b5 30%,#c98a58 60%,#7a4a2c 85%,#3d2b26 100%)}
</style>
</head>
<body>

<svg width="0" height="0" style="position:absolute" aria-hidden="true">
  <symbol id="i-pin" viewBox="0 0 32 32"><path d="M16 28s-8-8.5-8-15a8 8 0 0 1 16 0c0 6.5-8 15-8 15z"/><circle cx="16" cy="13" r="3"/></symbol>
  <symbol id="i-book" viewBox="0 0 32 32"><path d="M4 7h9a3 3 0 0 1 3 3v17a3 3 0 0 0-3-3H4z"/><path d="M28 7h-9a3 3 0 0 0-3 3v17a3 3 0 0 1 3-3h9z"/></symbol>
  <symbol id="i-briefcase" viewBox="0 0 32 32"><rect x="4" y="10" width="24" height="17" rx="2"/><path d="M12 10V7h8v3M4 17h24"/></symbol>
  <symbol id="i-person" viewBox="0 0 32 32"><circle cx="16" cy="11" r="5"/><path d="M7 27c0-5 4-8 9-8s9 3 9 8"/></symbol>
  <symbol id="i-cal" viewBox="0 0 32 32"><rect x="5" y="7" width="22" height="20" rx="1"/><path d="M5 13h22M11 4v5M21 4v5"/></symbol>
  <symbol id="i-cal-tick" viewBox="0 0 32 32"><rect x="5" y="7" width="22" height="20" rx="1"/><path d="M5 13h22M11 4v5M21 4v5M11 20l4 3 6-6"/></symbol>
  <symbol id="i-note" viewBox="0 0 32 32"><path d="M12 24V7l14-3v17"/><circle cx="9" cy="24" r="3"/><circle cx="23" cy="21" r="3"/></symbol>
  <symbol id="i-flag" viewBox="0 0 32 32"><path d="M8 28V5M8 6h16l-4 5 4 5H8"/></symbol>
</svg>

<!-- Hero screen -->
<section class="screen screen--night screen--hero" style="left:449px;top:124px">
  <div class="status"><span class="dots">•••</span><span>Lorem ipsum</span><span class="icons"><span class="wifi"></span><span class="battery"></span></span></div>
  <h1 class="screen-title" style="top:40px">Tell me about you</h1>
  <div class="card-grid" style="top:70px;left:9px;grid-template-columns:75px 75px;grid-auto-rows:68px;gap:6px">
    <div class="info-card"><svg><use href="#i-pin"/></svg>Places I’ve<br>Lived</div>
    <div class="info-card"><svg><use href="#i-book"/></svg>Schools I’ve<br>Attended</div>
    <div class="info-card"><svg><use href="#i-briefcase"/></svg>Places I’ve<br>Worked</div>
    <div class="info-card"><svg><use href="#i-person"/></svg>People I<br>Know</div>
    <div class="info-card"><svg><use href="#i-cal"/></svg>Events I’ve<br>Attended</div>
    <div class="info-card"><svg><use href="#i-cal-tick"/></svg>Events I’m<br>Attending</div>
    <div class="info-card"><svg><use href="#i-note"/></svg>Music I<br>Love</div>
    <div class="info-card"><svg><use href="#i-flag"/></svg>Teams I<br>Love</div>
  </div>
</section>

<div class="brand-band"></div>

<!-- Sign up -->
<section class="screen screen--deep" style="left:79px;top:660px">
  <div class="status"><span class="dots">•••</span><span>Lorem ipsum</span><span class="time">19:33</span><span class="icons"><span class="wifi"></span><span class="battery"></span></span></div>
  <svg class="back-arrow" viewBox="0 0 18 8" fill="none" stroke="#fff" stroke-width="1"><path d="M18 4H1M4 1L1 4l3 3"/></svg>
  <h1 class="signup-title">Sign Up</h1>
  <div class="field" style="top:75px">User Name<i></i></div>
  <div class="field" style="top:104px">Password<i></i></div>
  <div class="primary-btn" style="top:132px">Sign Up</div>
  <div class="remember"><span class="box"></span>Remember Me<a>Forgot Password?</a></div>
  <div class="divider-or">Or</div>
  <div class="connect-btn connect-btn--chatterloop" style="left:9px;width:160px;top:213px"><span class="mark"><span></span></span><span class="label">Connect With Chatterloop</span></div>
  <div class="connect-btn connect-btn--workvine" style="left:9px;width:160px;top:241px"><span class="mark"><span></span></span><span class="label">Connect With Workvine</span></div>
</section>

<!-- Category cards -->
<section class="screen screen--night" style="left:307px;top:660px">
  <div class="status"><span class="dots">•••</span><span>Lorem ipsum</span><span class="time">19:33</span><span class="icons"><span class="wifi"></span><span class="battery"></span></span></div>
  <h1 class="screen-title">Tell me about you</h1>
  <div class="card-grid">
    <div class="info-card"><svg><use href="#i-pin"/></svg>Places I’ve<br>Lived</div>
    <div class="info-card"><svg><use href="#i-book"/></svg>Schools I’ve<br>Attended</div>
    <div class="info-card"><svg><use href="#i-briefcase"/></svg>Places I’ve<br>Worked</div>
    <div class="info-card"><svg><use href="#i-person"/></svg>People I<br>Know</div>
    <div class="info-card"><svg><use href="#i-cal"/></svg>Events I’ve<br>Attended</div>
    <div class="info-card"><svg><use href="#i-cal-tick"/></svg>Events I’m<br>Attending</div>
    <div class="info-card"><svg><use href="#i-note"/></svg>Music I<br>Love</div>
    <div class="info-card"><svg><use href="#i-flag"/></svg>Teams I<br>Love</div>
  </div>
</section>

<!-- Places -->
<section class="screen screen--dusk" style="left:536px;top:660px">
  <div class="status"><span class="dots">•••</span><span>Lorem ipsum</span><span class="time">19:33</span><span class="icons"><span class="wifi"></span><span class="battery"></span></span></div>
  <div class="city-photo" role="img" aria-label="Photo of a city bridge at sunset"></div>
  <h1 class="screen-title">Places I’ve Lived</h1>
  <div class="chips" style="top:63px">
    <span class="chip">Chicago</span><span class="chip">Madrid</span>
    <span class="chip">Paris</span><span class="chip">Rio de Janiero</span>
  </div>
  <div class="search" style="top:116px"><div class="query">Londo</div><div class="suggestion">London, United Kingdom</div></div>
  <div class="connect-btn connect-btn--chatterloop" style="left:9px;width:159px;top:166px"><span class="mark"><span></span></span><span class="label">Connect With Chatterloop</span></div>
  <div class="connect-btn connect-btn--workvine" style="left:9px;width:159px;top:194px"><span class="mark"><span></span></span><span class="label">Connect With Workvine</span></div>
</section>

<!-- Music -->
<section class="screen screen--dusk" style="left:765px;top:660px">
  <div class="status"><span class="dots">•••</span><span>Lorem ipsum</span><span class="time">19:33</span><span class="icons"><span class="wifi"></span><span class="battery"></span></span></div>
  <div class="city-photo" role="img" aria-label="Photo of a city bridge at sunset"></div>
  <h1 class="screen-title">Music I Love</h1>
  <div class="chips" style="top:68px">
    <span class="chip">The Velvet Larks</span><span class="chip">Marisol</span>
    <span class="chip">Nickel Kid</span><span class="chip">Ray Calloway</span>
  </div>
  <div class="search" style="top:121px"><div class="query">Brittany Sparr</div><div class="suggestion">Brittany Sparrow</div></div>
  <div class="connect-btn connect-btn--chatterloop" style="left:9px;width:159px;top:171px"><span class="mark"><span></span></span><span class="label">Connect With Chatterloop</span></div>
  <div class="connect-btn connect-btn--tunevale" style="left:9px;width:159px;top:199px">CONNECT WITH TUNEVALE</div>
</section>

</body>
</html>
```